BOLD & MINIMALIST DESIGN NEEDED

We want a very bold but minimalistic business card design that is impactful and utilizes both sides of the business card. Our current logo is included for your use.

We want bold fonts and good use of negative space. We don't want the logo to overpower the design.

Target Market(s)

Professionals who are building new commercial buildings.

Industry/Entity Type

Construction

Contact Information for Business Card

Name, Title, email, office phone, cell phone, website

Font styles to use
Serif
Sans Serif

Requirements
Must have
• Bold design!

```html
<!DOCTYPE html>
<html lang="en">
<head>
<meta charset="utf-8">
<title>Ridgeline Design + Build — Business Card</title>
<link rel="stylesheet" href="https://fonts.googleapis.com/css2?family=Poppins:wght@400;500;700&family=Fira+Sans+Condensed:wght@600&display=swap">
<style>
  :root {
    --backdrop: #b7b7b7;
    --card-black: #0a0a0b;
    --card-white: #ffffff;
    --ink-white: #f4f4f2;
    --ink-black: #0d0d0d;
    --lime: #7dc52e;
    --lime-light: #b4de84;
    --rule: #5a5a5a;
  }
  * { box-sizing: border-box; margin: 0; padding: 0; }
  html, body { width: 1200px; height: 1200px; overflow: hidden; }
  body {
    background: var(--backdrop);
    font-family: "Poppins", sans-serif;
    position: relative;
  }
  .card {
    position: absolute;
    top: 303px;
    width: 369px;
    height: 594px;
    overflow: hidden;
  }
  .card--back { left: 200px; background: var(--card-black); }
  .card--front { left: 599px; width: 364px; background: var(--card-white); }

  .brand {
    position: absolute;
    left: 0; right: 0;
    text-align: center;
    font-family: "Poppins", sans-serif;
    font-weight: 700;
    line-height: 1;
  }
  .brand__name { font-size: 42px; letter-spacing: 1px; }
  .brand__tag { margin-top: 10px; font-size: 15px; letter-spacing: 7px; padding-left: 7px; }
  .card--back .brand { top: 468px; color: var(--ink-white); }
  .card--front .brand { top: 168px; color: var(--ink-black); }

  .front__band { position: absolute; left: 0; top: 300px; width: 364px; height: 45px; }
  .front__lower {
    position: absolute;
    left: 0; top: 344px;
    width: 364px; height: 250px;
    background: var(--card-black);
    color: var(--ink-white);
    text-align: center;
  }
  .person__name {
    margin-top: 30px;
    font-family: "Fira Sans Condensed", sans-serif;
    font-weight: 600;
    font-size: 24px;
    line-height: 1;
    letter-spacing: 0.5px;
  }
  .person__title {
    margin-top: 6px;
    font-size: 14px;
    font-weight: 500;
    color: var(--lime);
    line-height: 1;
  }
  .contact-icons {
    display: flex;
    align-items: center;
    justify-content: center;
    gap: 4px;
    margin-top: 17px;
  }
  .contact-icons__rule { width: 52px; height: 1px; background: var(--rule); margin: 0 7px; }
  .contact-icons__item {
    width: 25px; height: 25px;
    border-radius: 3px;
    background: var(--lime);
    display: flex; align-items: center; justify-content: center;
  }
  .contact-list { margin-top: 12px; list-style: none; font-size: 16.5px; line-height: 21.7px; }
  .contact-list .accent { color: var(--lime); }
</style>
</head>
<body>

  <section class="card card--back" aria-label="Card back">
    <div class="brand">
      <div class="brand__name">RIDGELINE</div>
      <div class="brand__tag">DESIGN + BUILD</div>
    </div>
  </section>

  <section class="card card--front" aria-label="Card front">
    <div class="brand">
      <div class="brand__name">RIDGELINE</div>
      <div class="brand__tag">DESIGN + BUILD</div>
    </div>

    <svg class="front__band" viewBox="0 0 364 45" aria-hidden="true">
      <defs>
        <linearGradient id="bandLeft" x1="0" x2="1" y1="0" y2="0">
          <stop offset="0" stop-color="var(--lime-light)"/>
          <stop offset="1" stop-color="var(--lime)"/>
        </linearGradient>
      </defs>
      <polygon points="0,45 182,17 182,45" fill="url(#bandLeft)"/>
      <polygon points="182,17 364,45 182,45" fill="var(--lime-light)"/>
    </svg>

    <div class="front__lower">
      <div class="person__name">DANIEL MOORE</div>
      <div class="person__title">MANAGING DIRECTOR</div>

      <div class="contact-icons">
        <span class="contact-icons__rule"></span>
        <span class="contact-icons__item" aria-label="Office phone">
          <svg width="15" height="15" viewBox="0 0 16 16"><path d="M2 6c0-2 3-3 6-3s6 1 6 3l-2 1-1-2H5L4 7z M4 8h8l1 5H3z" fill="#fff"/></svg>
        </span>
        <span class="contact-icons__item" aria-label="Mobile phone">
          <svg width="15" height="15" viewBox="0 0 16 16"><rect x="4.5" y="1.5" width="7" height="13" rx="1" fill="none" stroke="#fff" stroke-width="1.4"/><circle cx="8" cy="12.3" r="0.8" fill="#fff"/></svg>
        </span>
        <span class="contact-icons__item" aria-label="Email">
          <svg width="15" height="15" viewBox="0 0 16 16"><rect x="1.5" y="3.5" width="13" height="9" fill="none" stroke="#fff" stroke-width="1.3"/><path d="M1.5 3.5L8 9l6.5-5.5M1.5 12.5L6 8m8.5 4.5L10 8" fill="none" stroke="#fff" stroke-width="1.1"/></svg>
        </span>
        <span class="contact-icons__item" aria-label="Website">
          <svg width="15" height="15" viewBox="0 0 16 16"><circle cx="8" cy="8" r="6.5" fill="#fff"/><path d="M5 4c2 1 3 3 1 4s0 3 1 4M10 3c-1 2 1 3 3 3" fill="none" stroke="var(--lime)" stroke-width="1.3"/></svg>
        </span>
        <span class="contact-icons__rule"></span>
      </div>

      <ul class="contact-list">
        <li>044-555 010 200</li>
        <li>044-555 010 201</li>
        <li>info@ridgelinebuild.com</li>
        <li>www.<span class="accent">ridgelinebuild</span>.com</li>
      </ul>
    </div>
  </section>

</body>
</html>
```